Accounting firm needing business card / letterhead designed
Marcus L. Trenholm, CPA
marcus@veltrowledger.com
www.veltrowledger.com
842 E Alder Ave Calder Ridge, IN 43827
728-562-0974

```html
<!DOCTYPE html>
<html lang="en">
<head>
<meta charset="utf-8">
<title>Veltrow Ledger — Business Card</title>
<link href="https://fonts.googleapis.com/css2?family=Exo+2:wght@600&family=Roboto:wght@400&family=Roboto+Condensed:wght@500&display=swap" rel="stylesheet">
<style>
  :root {
    --backdrop: #c9c9c9;
    --lime: #8dc63f;
    --navy: #261f63;
    --paper: #f3f3f3;
    --white: #ffffff;
    --rule: #9a9a9a;
  }
  * { margin: 0; padding: 0; box-sizing: border-box; }
  html, body { width: 1200px; height: 960px; overflow: hidden; }
  body {
    position: relative;
    background: var(--backdrop);
    font-family: "Roboto", Arial, sans-serif;
  }
  .card {
    position: absolute;
    left: 320px;
    width: 600px;
    height: 342px;
    border-radius: 18px;
    overflow: hidden;
  }
  .card-front { top: 108px; background: var(--lime); }
  .card-back  { top: 493px; background: var(--paper); }

  .brand-name {
    font-family: "Exo 2", Arial, sans-serif;
    font-weight: 600;
    color: var(--navy);
    text-transform: uppercase;
    white-space: nowrap;
  }
  .card-front .brand-name {
    position: absolute;
    left: 0; right: 0;
    top: 138px;
    text-align: center;
    font-size: 36px;
    letter-spacing: 2px;
  }
  .front-web {
    position: absolute;
    left: 0; right: 0;
    top: 281px;
    text-align: center;
    color: var(--white);
    font-size: 14px;
    letter-spacing: 6.2px;
  }

  .card-back .brand-name {
    position: absolute;
    right: 38px;
    top: 62px;
    font-size: 26px;
    letter-spacing: 1.5px;
  }
  .name-marker {
    position: absolute;
    left: 0; top: 96px;
    width: 17px; height: 23px;
    background: linear-gradient(to right, var(--navy) 0 13px, transparent 13px 14px, var(--lime) 14px 17px);
  }
  .holder-name {
    position: absolute;
    left: 31px; top: 93px;
    font-family: "Roboto Condensed", Arial, sans-serif;
    font-weight: 500;
    font-size: 21px;
    color: var(--navy);
  }
  .name-rule {
    position: absolute;
    left: 32px; right: 38px; top: 127px;
    height: 1px;
    background: var(--rule);
  }
  .contact-band {
    position: absolute;
    left: 0; right: 0; bottom: 0;
    height: 109px;
    background: var(--navy);
    color: var(--white);
    font-size: 14.5px;
  }
  .contact-list {
    position: absolute;
    left: 32px; top: 24px;
    list-style: none;
  }
  .contact-list li {
    display: flex;
    align-items: center;
    height: 19px;
  }
  .contact-list svg { width: 13px; height: 13px; margin-right: 9px; fill: var(--white); }
  .address {
    position: absolute;
    right: 38px; top: 43px;
    text-align: right;
    font-style: normal;
    line-height: 19px;
  }
</style>
</head>
<body>
  <section class="card card-front">
    <div class="brand-name">Veltrow Ledger</div>
    <div class="front-web">www.veltrowledger.com</div>
  </section>

  <section class="card card-back">
    <div class="brand-name">Veltrow Ledger</div>
    <div class="name-marker"></div>
    <div class="holder-name">Marcus L. Trenholm, CPA</div>
    <div class="name-rule"></div>

    <div class="contact-band">
      <ul class="contact-list">
        <li>
          <svg viewBox="0 0 16 16" aria-hidden="true"><path d="M3.6 1.2l2.3 2.6-1.3 1.8c.9 2 2.6 3.7 4.6 4.6l1.8-1.3 2.6 2.3-1.3 2.3C7 15.2 0.8 9 1.3 2.5z"/></svg>
          728-562-0974
        </li>
        <li>
          <svg viewBox="0 0 16 16" aria-hidden="true"><path d="M1 3h14v1.2L8 8.6 1 4.2z"/><path d="M1 5.6l7 4.4 7-4.4V13H1z"/></svg>
          marcus@veltrowledger.com
        </li>
        <li>
          <svg viewBox="0 0 16 16" aria-hidden="true"><circle cx="8" cy="8" r="7"/><path d="M4 5c1 0 2 1 2 2s1 1 1 2-1 2 0 3" stroke="#261f63" stroke-width="1.3" fill="none"/><path d="M10 3c0 1 1 2 2 2" stroke="#261f63" stroke-width="1.3" fill="none"/></svg>
          www.veltrowledger.com
        </li>
      </ul>
      <address class="address">
        842 E Alder Ave<br>
        Calder Ridge, IN 43827
      </address>
    </div>
  </section>
</body>
</html>
```